Brochure condensed from the PDF marketing

An organised brochure with 4 x banner heading for the various portfolios,
Condensed and made into a 4 page booklet or neat and tidy brochure display that can be easily emailed to prospective customers. The brochure should be neat and professional similar content to the website to send the 4 x Portfolios to the various Industry Categories, thank you

** Ive just uploaded a couple of extra photos for the ' Our Services ' area on the Brochure, pls add the ice cream one for the ' Parfait Cleaning and Sanitisation Services, and on the ' Our Services' category for the High pressure Gurney and Playground Cleaning pls add a fun photo for example the one I sent with people having fun on the playground equipment, **

HI KT Designer The brochure design is for my facebook title page /Users/user/Desktop/Screenshot 2020-05-05 at 9.22.39 PM.png Under Brightwell Facebook Design (Contest) DO you have a direct email, its very difficult to keep posing images and updates here Thank you Imogen @ Brightwell.

Target Market(s)

Cleaning Services

Font styles to use
Serif

Requirements
Must have
• Look professional and neat and tidy brochure booklet for marketing on email to prospective customers.

```html
<!DOCTYPE html>
<html lang="en">
<head>
<meta charset="utf-8">
<title>Brightwell Brochure</title>
<link href="https://fonts.googleapis.com/css2?family=Noto+Serif:wght@400;700&family=Roboto+Condensed:wght@300;400;700&display=swap" rel="stylesheet">
<style>
:root{
  --orange:#ee5a16;
  --orange-soft:#f37a3f;
  --navy:#163d7a;
  --navy-deep:#123a78;
  --ink:#1d3b6e;
  --paper:#f4f5f7;
  --backdrop:#a9a9a9;
  --serif:"Noto Serif", Georgia, serif;
  --cond:"Roboto Condensed", Arial, sans-serif;
}
*{box-sizing:border-box;margin:0;padding:0}
html,body{width:1200px;height:2769px;overflow:hidden}
body{background:var(--backdrop);position:relative;font-family:var(--serif);color:var(--ink)}
.page{position:absolute;width:522px;height:686px;background:var(--paper);overflow:hidden;box-shadow:0 3px 10px rgba(0,0,0,.25)}
.page--hero{left:327px;top:165px;transform:scale(1.0805);transform-origin:0 0}
.page--cover{left:61px;top:1111px}
.page--about{left:610px;top:1111px}
.page--services{left:61px;top:1824px}
.page--back{left:612px;top:1824px;background:var(--navy-deep);color:#fff}
.abs{position:absolute}

/* brand */
.brand{position:absolute;display:flex;align-items:center;gap:10px}
.brand__dot{width:40px;height:40px;border-radius:50%;background:var(--navy)}
.brand__name{font-family:var(--serif);color:var(--navy);font-weight:400;line-height:1}
.cover__brand{left:95px;top:32px}
.cover__brand .brand__name{font-size:46px}
.cover__url{position:absolute;left:158px;top:84px;font-size:13px;letter-spacing:4.2px;color:var(--ink)}
.cover__rule{position:absolute;left:52px;top:120px;width:470px;height:6px;background:var(--orange)}

/* cover grid */
.photo{position:absolute}
.photo--kitchen{left:0;top:126px;width:310px;height:147px;clip-path:polygon(0 0,100% 0,91% 100%,0 100%);background:linear-gradient(135deg,#6d6259,#b3aca4 55%,#3d3a3a)}
.photo--office{left:272px;top:126px;width:250px;height:147px;clip-path:polygon(15% 0,100% 0,100% 100%,3% 100%);background:linear-gradient(135deg,#e3e5e8,#9fa9b6 60%,#3f5171)}
.photo--hood{left:0;top:326px;width:270px;height:133px;clip-path:polygon(0 0,100% 0,88% 100%,0 100%);background:linear-gradient(135deg,#cfd2d6,#8c9196 60%,#e1e4e7)}
.photo--playground{left:240px;top:326px;width:282px;height:133px;clip-path:polygon(18% 0,100% 0,100% 100%,0 100%);background:linear-gradient(135deg,#c62e32,#4b4f8e 50%,#d9d4d0)}
.band{position:absolute;left:0;width:522px;background:linear-gradient(90deg,var(--orange-soft),var(--orange))}
.band--top{top:273px;height:53px}
.band--bottom{top:459px;height:55px}
.band__gap{position:absolute;top:0;width:4px;height:100%;background:#fff;transform:skewX(-22deg)}
.label{position:absolute;color:#fff;font-family:var(--cond);line-height:1.1}
.label span{display:block;font-weight:300;font-size:16px}
.label strong{display:block;font-weight:700;font-size:17px}
.label--right{text-align:right}

.welcome{position:absolute;left:0;width:522px;text-align:center}
.welcome__intro{top:554px;font-size:40px;color:var(--navy)}
.welcome__title{top:592px;font-size:54px;font-weight:700;letter-spacing:1px;line-height:1}
.welcome__title .o{color:var(--orange)} .welcome__title .n{color:var(--navy)}
.welcome__contact{top:654px;font-size:13px;color:var(--navy)}

/* about page */
.about__photo{left:0;top:0;width:228px;height:250px;background:linear-gradient(150deg,#cfd3d9,#7a8fb8 55%,#3c5ea8);border-radius:0 0 120px 0}
.about__heading{left:264px;top:60px;font-size:19px;font-weight:700;line-height:1;color:var(--navy)}
.o{color:var(--orange)}
.about__years{left:264px;top:110px;font-family:var(--cond);font-size:10px;color:var(--orange)}
.about__intro{left:264px;top:132px;width:212px;font-family:var(--cond);font-size:10px;line-height:1.3;text-align:justify;color:var(--ink)}
.pillar{position:absolute;top:262px;width:154px;height:258px;background:var(--navy)}
.pillar__icon{height:80px;background:var(--orange);display:flex;align-items:center;justify-content:center}
.pillar__title{font-size:14px;font-weight:700;color:#fff;text-align:center;margin-top:10px}
.pillar__text{font-family:var(--cond);font-size:9.5px;line-height:1.28;color:#fff;text-align:center;padding:7px 14px 0}
.values__title{left:25px;top:533px;font-size:19px;font-weight:700;color:var(--navy)}
.values__list{left:25px;top:565px;width:480px;font-family:var(--cond);font-size:8.6px;line-height:1.65;color:var(--navy);list-style:none}
.values__list b{font-weight:700}

.footer{position:absolute;left:20px;top:645px;width:502px;height:24px}
.footer .brand{left:0;top:0;gap:6px}
.footer .brand__dot{width:20px;height:20px}
.footer .brand__name{font-size:20px}
.footer__line{position:absolute;left:150px;top:12px;width:352px;height:1px;background:var(--navy)}
.footer__num{position:absolute;left:442px;top:2px;width:22px;height:22px;background:var(--orange);color:#fff;font-family:var(--cond);font-weight:700;font-size:14px;text-align:center;line-height:22px}

/* services page */
.services__title{left:0;top:18px;width:522px;text-align:center;font-size:19px;font-weight:700;color:var(--navy)}
.thumb{position:absolute;top:52px;width:104px;height:100px;border:4px solid #fff;box-shadow:0 1px 4px rgba(0,0,0,.35)}
.thumb--parfait{left:28px;background:linear-gradient(135deg,#314d75,#8aa0bd)}
.thumb--general{left:148px;background:linear-gradient(135deg,#eef1f4,#9bb2c9)}
.thumb--gurney{left:268px;background:linear-gradient(135deg,#7b7a5a,#c8c3b3)}
.thumb--kitchen{left:388px;background:linear-gradient(135deg,#a5a9ad,#e2e3e5)}
.caption{position:absolute;top:158px;width:110px;text-align:center;font-size:10.5px;font-weight:700;line-height:1.12;color:var(--navy)}
.safety{position:absolute;left:0;top:207px;width:522px;height:180px;background:var(--navy-deep);color:#fff;text-align:center;padding:12px 28px 0}
.safety h2{font-size:18px;margin-bottom:6px}
.safety p{font-family:var(--cond);font-size:8.6px;line-height:1.3;margin-bottom:8px}
.pricing__title{left:0;top:394px;width:522px;text-align:center;font-size:18px;font-weight:700;color:var(--navy)}
.prices{position:absolute;left:25px;top:419px;display:flex;gap:5px}
.price{width:74px;height:82px;background:#fff;border:1px solid var(--navy);padding:5px 5px;font-size:7px;font-weight:700;line-height:1.1;color:var(--navy)}
.price__amount{display:block;color:var(--orange);font-size:10px;margin-top:14px}
.price__note{display:block;font-weight:400;font-size:5.5px;color:#777}
.pricing__foot{left:25px;top:508px;font-family:var(--cond);font-size:7px;color:var(--navy)}
.stories__title{left:25px;top:526px;font-size:18px;font-weight:700;color:var(--navy)}
.stories__text{left:25px;top:551px;width:318px;font-family:var(--cond);font-size:7.6px;line-height:1.3;color:var(--navy)}
.stories__text p{margin-bottom:4px}
.partner{position:absolute;left:360px;top:563px;display:flex;align-items:center;gap:6px}
.partner__mark{width:34px;height:34px;background:#c8102e}
.partner__name{font-family:var(--serif);font-weight:700;font-size:15px;color:#c8102e}

/* back page */
.back__brand{left:110px;top:72px;gap:12px}
.back__brand .brand__dot{background:#fff;width:46px;height:46px}
.back__brand .brand__name{color:#fff;font-size:38px}
.back__contact{left:0;top:160px;width:522px;text-align:center;font-size:14px;line-height:1.22}
</style>
</head>
<body>

<!-- Hero cover -->
<section class="page page--hero" aria-label="Front cover">
  <div class="brand cover__brand"><span class="brand__dot"></span><span class="brand__name">Brightwell</span></div>
  <div class="cover__url">www.brightwell.com.au</div>
  <div class="cover__rule"></div>
  <div class="photo photo--kitchen" role="img" aria-label="Commercial soft-serve machine in a kitchen"></div>
  <div class="photo photo--office" role="img" aria-label="Cleaners working in an office"></div>
  <div class="band band--top"><span class="band__gap" style="left:281px"></span></div>
  <div class="label" style="left:24px;top:280px"><span>EQUIPMENT CLEANING &amp;</span><strong>SANITISATION SERVICES</strong></div>
  <div class="label label--right" style="right:22px;top:280px"><span>GENERAL CLEANING &amp; PROPERTY</span><strong>FACILITIES MANAGEMENT</strong></div>
  <div class="photo photo--hood" role="img" aria-label="Kitchen exhaust hood being cleaned"></div>
  <div class="photo photo--playground" role="img" aria-label="Family enjoying playground equipment"></div>
  <div class="band band--bottom"><span class="band__gap" style="left:226px"></span></div>
  <div class="label" style="left:24px;top:467px"><span>KITCHEN DETAIL CLEANING</span><strong>SERVICES</strong></div>
  <div class="label label--right" style="right:22px;top:467px"><span>HIGH PRESSURE GURNEY &amp; PLAYGROUND</span><strong>CLEANING SERVICES</strong></div>
  <div class="welcome welcome__intro">Welcome to</div>
  <div class="welcome welcome__title"><span class="o">BRIGHT</span><span class="n">WELL</span></div>
  <div class="welcome welcome__contact">Customer Service: 1300 555 018 &nbsp;|&nbsp; Email: service@brightwell.com.au</div>
</section>

<!-- Cover in spread -->
<section class="page page--cover" aria-label="Front cover">
  <div class="brand cover__brand"><span class="brand__dot"></span><span class="brand__name">Brightwell</span></div>
  <div class="cover__url">www.brightwell.com.au</div>
  <div class="cover__rule"></div>
  <div class="photo photo--kitchen" role="img" aria-label="Commercial soft-serve machine in a kitchen"></div>
  <div class="photo photo--office" role="img" aria-label="Cleaners working in an office"></div>
  <div class="band band--top"><span class="band__gap" style="left:281px"></span></div>
  <div class="label" style="left:24px;top:280px"><span>EQUIPMENT CLEANING &amp;</span><strong>SANITISATION SERVICES</strong></div>
  <div class="label label--right" style="right:22px;top:280px"><span>GENERAL CLEANING &amp; PROPERTY</span><strong>FACILITIES MANAGEMENT</strong></div>
  <div class="photo photo--hood" role="img" aria-label="Kitchen exhaust hood being cleaned"></div>
  <div class="photo photo--playground" role="img" aria-label="Family enjoying playground equipment"></div>
  <div class="band band--bottom"><span class="band__gap" style="left:226px"></span></div>
  <div class="label" style="left:24px;top:467px"><span>KITCHEN DETAIL CLEANING</span><strong>SERVICES</strong></div>
  <div class="label label--right" style="right:22px;top:467px"><span>HIGH PRESSURE GURNEY &amp; PLAYGROUND</span><strong>CLEANING SERVICES</strong></div>
  <div class="welcome welcome__intro">Welcome to</div>
  <div class="welcome welcome__title"><span class="o">BRIGHT</span><span class="n">WELL</span></div>
  <div class="welcome welcome__contact">Customer Service: 1300 555 018 &nbsp;|&nbsp; Email: service@brightwell.com.au</div>
</section>

<!-- Page 1 -->
<section class="page page--about" aria-label="Working with Brightwell">
  <div class="abs about__photo" role="img" aria-label="Carpet and floor cleaning scenes"></div>
  <h1 class="abs about__heading">WORKING<br>WITH <span class="o">BRIGHT</span>WELL</h1>
  <p class="abs about__years">We have been in business for 15 years.</p>
  <p class="abs about__intro">Our people are professional, reliable and service orientated. In every interaction on site, receiving help from our service support staff or rolling-out new cleaning sites, we are focused on delivering a positive &amp; high quality customer service experience.</p>

  <div class="pillar" style="left:25px">
    <div class="pillar__icon"><svg width="40" height="46" viewBox="0 0 40 46"><g fill="#fff"><circle cx="20" cy="10" r="5"/><circle cx="11" cy="18" r="5"/><circle cx="29" cy="18" r="5"/><rect x="18" y="20" width="4" height="14"/><path d="M8 34h24l-3 10H11z"/></g></svg></div>
    <h3 class="pillar__title">OUR PURPOSE</h3>
    <p class="pillar__text">Our purpose is to provide high quality hygiene and sanitisation services to each of our dedicated portfolios across equipment cleaning services, gurney and playground cleaning, general commercial cleaning and property facility maintenance services to create the most effective results for our customers and community.</p>
  </div>
  <div class="pillar" style="left:184px">
    <div class="pillar__icon"><svg width="56" height="56" viewBox="0 0 56 56"><path fill="#fff" d="M28 0l5 23 23 5-23 5-5 23-5-23L0 28l23-5z"/></svg></div>
    <h3 class="pillar__title">OUR VISION</h3>
    <p class="pillar__text">Sustainable commercial environment and food service equipment cleaning and sanitisation service provider. Recognised as being the most effective brand, growing employees and giving back to the community for generations to come.</p>
  </div>
  <div class="pillar" style="left:343px">
    <div class="pillar__icon"><svg width="56" height="56" viewBox="0 0 56 56"><circle cx="28" cy="28" r="25" fill="none" stroke="#fff" stroke-width="3"/><path fill="#fff" d="M40 16L31 31 16 40 25 25z"/></svg></div>
    <h3 class="pillar__title">OUR STRATEGY</h3>
    <p class="pillar__text">To differentiate ourselves through a prevailing focus on customer service, in everything we do and every interaction we have to be a positive and professional experience. We treat our people as skilled cleaning professionals who are the foundation of our companys sustainability.</p>
  </div>

  <h2 class="abs values__title">OUR <span class="o">VALUES</span></h2>
  <ul class="abs values__list">
    <li><b>Safety and the Environment</b> – We are committed to providing a safe and healthy working environment.</li>
    <li><b>Professionalism/Integrity</b> – We are committed to doing what we say we are going to do.</li>
    <li><b>Sustainability</b> – Achieving results that are mutually beneficial for our employees, our customers, our partners and the company.</li>
    <li><b>Positive Working Relationships</b> – Having relationships that focus on shared goals and creation of value for all parties.</li>
    <li><b>Respect for Each Other</b> – The embracing of diversity, enriched by openness, sharing, trust, teamwork and involvement.</li>
  </ul>

  <div class="footer">
    <div class="brand"><span class="brand__dot"></span><span class="brand__name">Brightwell</span></div>
    <div class="footer__line"></div>
    <div class="footer__num">1</div>
  </div>
</section>

<!-- Page 2 -->
<section class="page page--services" aria-label="Our services">
  <h2 class="abs services__title">OUR <span class="o">SERVICES</span></h2>
  <div class="thumb thumb--parfait" role="img" aria-label="Ice cream being served from a machine"></div>
  <div class="thumb thumb--general" role="img" aria-label="Cleaners in an office"></div>
  <div class="thumb thumb--gurney" role="img" aria-label="Pressure washing outdoor ground"></div>
  <div class="thumb thumb--kitchen" role="img" aria-label="Commercial kitchen"></div>
  <p class="caption" style="left:25px">Equipment Cleaning &amp; Sanitisation Services</p>
  <p class="caption" style="left:145px">General Cleaning &amp; Property Facilities Management</p>
  <p class="caption" style="left:265px">High Pressure gurney &amp; play ground equipment Cleaning</p>
  <p class="caption" style="left:385px">Kitchen Detail Cleaning Service</p>

  <div class="safety">
    <h2>SAFETY &amp; <span class="o">COMPLIANCE</span></h2>
    <p>Brightwell values safety and environment. We have an overriding commitment to health, safety and environmental responsibility.</p>
    <p>Each member of our company community undergoes a yearly on-line safety refresher course, and performs a routine reflection safety check and risk assessment at each clients site on attending work each day. We have safety work method statements in place and work on ensuring our people work safely on site through practical application of safety steps, safety shoes and appropriate personal protection equipment (PPE) work gear.</p>
    <p>Brightwell is covered with $20,000,000 General and Product Liability coverage through Harbourline Insurance and has work cover in place for all our employees across Sydney, Brisbane, Melbourne and Adelaide.</p>
    <p>Brightwell employees always aspire to work safely whilst on client sites.</p>
  </div>

  <h2 class="abs pricing__title">CURRENT <span class="o">PRICING</span></h2>
  <div class="prices">
    <div class="price">General Office Cleaning<span class="price__amount">$ 70.00</span><span class="price__note">+ GST/hour</span></div>
    <div class="price">Parfait Equipment Cleaning Single Unit<span class="price__amount">$ 120.00</span><span class="price__note">+ GST/service</span></div>
    <div class="price">Parfait Equipment Cleaning Double Unit<span class="price__amount" style="margin-top:6px">$ 180.00</span><span class="price__note">+ GST/fortnightly service</span><span class="price__amount" style="margin-top:2px">$ 200.00</span><span class="price__note">+ GST/monthly service</span></div>
    <div class="price">Gurney High Pressure work<span class="price__amount">$ 100.00</span><span class="price__note">+ GST/hour</span></div>
    <div class="price">Builders Cleaning Services<span class="price__amount">$ 100.00</span><span class="price__note">+ GST/hour</span><span class="price__note" style="margin-top:4px">* Any rubbish removal fee for waste disposal</span></div>
    <div class="price">Kitchen Detail Foam and Scrub<span class="price__amount">$ 80.00</span><span class="price__note">+ GST/hour</span></div>
  </div>
  <p class="abs pricing__foot">* &gt; 50km travel fee and public holiday rates apply in accordance to the Cleaning Services Award, 2010.</p>

  <h2 class="abs stories__title">OUR <span class="o">SUCCESS STORIES</span></h2>
  <div class="abs stories__text">
    <p>Project Management</p>
    <p>We successfully managed the roll out of 200 Equipment Asset Parfait Crusher Machines, 191 K Velluto Machines for Rooster &amp; Co from 2012 to 2019 for the facilities department. We resourced the project with the most effective talent including skilled mechanics, mechanical engineers and professional tradespeople.</p>
    <p>Brightwell was responsible for the regular fortnightly cleaning and maintenance sanitisation services including regular 6 monthly tune up kit installations for the Rooster &amp; Co Community across Sydney, Brisbane, Melbourne and Adelaide.</p>
  </div>
  <div class="partner"><span class="partner__mark"></span><span class="partner__name">Rooster &amp; Co</span></div>

  <div class="footer">
    <div class="brand"><span class="brand__dot"></span><span class="brand__name">Brightwell</span></div>
    <div class="footer__line"></div>
    <div class="footer__num">2</div>
  </div>
</section>

<!-- Back cover -->
<section class="page page--back" aria-label="Back cover">
  <div class="brand back__brand"><span class="brand__dot"></span><span class="brand__name">Brightwell</span></div>
  <div class="abs back__contact">
    Sydney | Brisbane | Melbourne | Adelaide<br>
    Landline: 1300 555 018<br>
    Mobile: 0400 555 274<br>
    Email: service@brightwell.com.au<br>
    www.brightwell.com.au
  </div>
</section>

</body>
</html>
```